Landing Page Design for Adult Dating Age Verification (18+)

The objective of this task is to design a visually appealing pre-landing page for the adult dating site "Quillmera (site: https://quillmera.com/)" with an age verification mechanism. The pre-landing page will feature two buttons that redirect visitors to the main offer. The design should also include a footer block that includes links to the terms of use, privacy policy, and contact us pages.

Design Requirements:
Develop an age verification section prominently displayed on the pre-landing page.
Design the section to include two buttons labeled "Yes" and "No" for visitors to confirm their age.
Ensure the section is visually appealing and clearly communicates the purpose of age verification.

Visual Appeal:
Create a visually appealing design that aligns with the branding and theme of the "Quillmera" adult dating site.
Use suitable color schemes, typography, and graphics to enhance the overall visual appeal of the pre-landing page.

Layout and Navigation:
Design an engaging and intuitive layout that encourages visitors to interact with the page and proceed to the main offer.
Ensure clear and visible navigation elements that direct visitors to the main offer or provide additional information.

Responsive Design:
Develop a responsive design that provides a seamless user experience across various devices, including desktop and mobile.
Ensure the design elements and layout adapt well to different screen sizes and resolutions.

File Formats and Assets:
Deliver the final design in PSD, AI, or Sketch format, ensuring that the files are well-organized and layered.
Include any necessary images or assets used in the design, ensuring they are of high quality and optimized for web use.

```html
<!DOCTYPE html>
<html lang="en">
<head>
<meta charset="utf-8">
<title>Quillmera — Age Verification</title>
<link rel="stylesheet" href="https://fonts.googleapis.com/css2?family=EB+Garamond:wght@400;500;700&family=Marcellus&display=swap">
<style>
  :root {
    --cream: #f0ebe8;
    --lilac: #d5b5d8;
    --ink: #1f1d22;
    --night: #1b2130;
    --umber: #4a3431;
    --plum: #5a3f45;
  }
  * { box-sizing: border-box; margin: 0; padding: 0; }
  html, body { width: 1200px; height: 658px; overflow: hidden; }
  body { font-family: "EB Garamond", Georgia, serif; color: var(--ink); background: var(--cream); position: relative; }

  .site-header {
    position: absolute; left: 0; top: 0; width: 1200px; height: 72px;
    background: var(--cream);
  }
  .brand {
    position: absolute; left: 100px; top: 14px;
    display: flex; align-items: center; gap: 8px;
    text-decoration: none; color: var(--ink);
  }
  .brand-dot { width: 30px; height: 30px; border-radius: 50%; background: var(--lilac); }
  .brand-name { font-family: "Marcellus", Georgia, serif; font-size: 25px; letter-spacing: 0.5px; color: var(--ink); }
  .header-nav { position: absolute; right: 99px; top: 16px; display: flex; align-items: center; gap: 17px; }
  .nav-link { font-size: 22px; font-weight: 500; color: var(--ink); text-decoration: none; }
  .nav-button {
    display: inline-flex; align-items: center; justify-content: center;
    width: 127px; height: 38px; border-radius: 6px;
    background: var(--lilac); color: var(--ink);
    font-size: 22px; font-weight: 500; text-decoration: none;
  }

  .hero { position: absolute; left: 0; top: 72px; width: 1200px; height: 586px; }
  .hero-photo {
    position: absolute; inset: 0;
    background:
      radial-gradient(ellipse at 62% 55%, #b48e7e 0%, rgba(120,86,80,0.6) 22%, transparent 45%),
      radial-gradient(ellipse at 80% 70%, var(--plum) 0%, transparent 55%),
      linear-gradient(100deg, var(--night) 0%, #2a2a33 40%, var(--umber) 70%, #2d2a31 100%);
  }

  .age-gate { position: absolute; left: 75px; top: 59px; width: 470px; height: 425px; }
  .age-gate svg { position: absolute; left: 0; top: 0; }
  .age-question {
    position: absolute; left: 0; width: 448px; top: 92px;
    text-align: center; font-weight: 700; font-size: 31px; line-height: 48px;
    letter-spacing: -0.6px; color: var(--ink); text-transform: uppercase;
  }
  .age-button {
    position: absolute; left: 166px; width: 115px; height: 48px; border-radius: 6px;
    display: flex; align-items: center; justify-content: center;
    font-size: 24px; text-decoration: none;
  }
  .age-button--yes { top: 199px; background: var(--ink); color: var(--cream); }
  .age-button--no { top: 260px; background: var(--cream); color: var(--ink); }

  .site-footer {
    position: absolute; left: 0; bottom: 0; width: 1200px; height: 30px;
    display: flex; align-items: center; justify-content: center; gap: 22px;
    font-size: 13px; color: var(--cream);
  }
  .footer-link { color: var(--cream); text-decoration: none; }
  .footnote { position: absolute; right: 12px; bottom: 8px; font-size: 12px; color: var(--cream); }
</style>
</head>
<body>
  <header class="site-header">
    <a class="brand" href="https://quillmera.com/">
      <span class="brand-dot"></span>
      <span class="brand-name">Quillmera</span>
    </a>
    <nav class="header-nav">
      <a class="nav-link" href="#">Sign in</a>
      <a class="nav-button" href="#">Join Now</a>
    </nav>
  </header>

  <main class="hero">
    <div class="hero-photo" role="img" aria-label="Photo of an embracing couple on a bed in a dim loft bedroom with brick walls and plants"></div>

    <section class="age-gate">
      <svg width="470" height="425" viewBox="0 0 470 425" aria-hidden="true">
        <path transform="translate(10 0)" fill="var(--cream)" d="M230 60 C190 10 120 -5 60 20 C10 45 -5 110 10 165 C30 240 140 340 230 422 C320 340 430 240 450 165 C465 110 450 45 400 20 C340 -5 270 10 230 60 Z"/>
        <path fill="var(--lilac)" d="M224 58 C186 10 118 -4 60 20 C10 45 -5 110 10 165 C30 240 136 338 224 418 C312 338 418 240 438 165 C453 110 438 45 390 20 C332 -4 262 10 224 58 Z"/>
      </svg>
      <h1 class="age-question">Are you 18 years of<br>age or older</h1>
      <a class="age-button age-button--yes" href="https://quillmera.com/">Yes</a>
      <a class="age-button age-button--no" href="#">No</a>
    </section>

    <footer class="site-footer">
      <a class="footer-link" href="#">Terms of Use</a>
      <a class="footer-link" href="#">Privacy Policy</a>
      <a class="footer-link" href="#">Contact Us</a>
    </footer>
    <span class="footnote">C 25</span>
  </main>
</body>
</html>
```